Kessara Investment Brochure for investment promotion

We need an investment manual to sell the potential of Kessara state (a state in Nigeria) to investors around the world. This manual / brochure should be top class and have a premium feel.

We have developed the content as attached and all that is required is to fit the content into a brochure format.
The brochure should be top class, easy to read and very friendly to investors

Target Market(s)

World Investors

Industry/Entity Type

Investment

Requirements
Must have
• Kessara State Logo (Can find online), Kessara Tower (can find online). Premium feel and look. design should be clean, no clutter. General images that represent investment sectors
Nice to have
• Pictures
Should not have
• Images of white men.

```html
<!DOCTYPE html>
<html lang="en">
<head>
<meta charset="utf-8">
<title>Industry Overview / Investment Opportunities</title>
<link href="https://fonts.googleapis.com/css2?family=Open+Sans:wght@400;600;700&display=swap" rel="stylesheet">
<style>
  :root {
    --brand-green: #2f8a3c;
    --brand-green-dark: #236b2e;
    --text: #3a3a3a;
    --page: #ffffff;
  }
  * { box-sizing: border-box; margin: 0; padding: 0; }
  html, body { width: 849px; height: 1200px; overflow: hidden; background: var(--page); }
  body { font-family: "Open Sans", Arial, sans-serif; color: var(--text); }
  .page { position: relative; width: 849px; height: 1200px; }
  .page-header {
    height: 58px; background: var(--brand-green);
    display: flex; align-items: center; padding: 0 32px;
  }
  .page-header h1 { color: #fff; font-size: 24px; font-weight: 400; letter-spacing: 0.2px; }
  .content { padding: 14px 32px 0; }
  .section-title {
    color: var(--brand-green); font-size: 19px; font-weight: 700; margin-bottom: 6px;
  }
  .content p { font-size: 13.4px; line-height: 1.42; margin-bottom: 16px; }
  .section + .section { margin-top: 10px; }
  .opportunities { list-style: none; margin: -8px 0 0 10px; }
  .opportunities li {
    position: relative; font-size: 13.4px; line-height: 1.42; padding-left: 22px; margin-bottom: 3px;
  }
  .opportunities li::before {
    content: ""; position: absolute; left: 4px; top: 7px;
    width: 6px; height: 6px; border-radius: 50%; background: var(--text);
  }
  .photo-row {
    position: absolute; top: 905px; left: 127px;
    display: flex; gap: 16px;
  }
  .photo { height: 285px; }
  .photo-factory { width: 283px; background: linear-gradient(160deg, #e8e6e0 0%, #c9cfc9 45%, #7a8f86 100%); }
  .photo-farm { width: 340px; background: linear-gradient(180deg, #b9c7b5 0%, #5f8a45 45%, #3d6a2c 100%); }
</style>
</head>
<body>
<div class="page">
  <header class="page-header">
    <h1>Industry Overview / Investment Opportunities</h1>
  </header>

  <main class="content">
    <section class="section">
      <h2 class="section-title">Manufacturing</h2>
      <p>The industrial center of the state is in Umora, with garment manufacturing, pharmaceuticals, Personal Care, Home Care, Food and Beverages, footwear and other leather products among the prominent commercial activities. The manufacturing sector has huge potentials yet to be fully tapped and still holds enormous opportunities for investors.</p>
      <p>The Umora leather and Garment industry is said to be the largest in West Africa, with a production capacity of about one million pairs of shoes per week, for local and international markets. This industry is made up of over 120,000 Entrepreneurs with average staff strength of 4.3 persons.</p>
      <p>Kessara has huge potential in the manufacturing sectordriven by availability of raw materials and a lot of manufacturing assets for Metallurgical, Ceramics, Brewing and Textile Industry, which are available for re-ignition through partnerships</p>
    </section>

    <section class="section">
      <h2 class="section-title">Agriculture</h2>
      <p>Agriculture is the second largest sector of Kessara economy employing about 70% of the state workforce and contributing about 27% of the GDP. This is predominantly subsistence, which leaves room for investment opportunities.</p>
      <p>There is incredible potential investment in mechanized farms with great potential for products at scale that would serve the rest of the country and even provide for export.Kessara state has adequate seasonal rainfall, with highly arable land that can grow yam, maize, potatoe, rice, cashew, plantain, palm oil and cassava.</p>
      <p>There are massive opportunities for private sector participation through partnerships or direct investment with Kessara State Government for development of the agricultural sector. The opportunities include:</p>
      <ul class="opportunities">
        <li>Commercial farming of key produce with comparative advantages including Cassava, Maize, Yam, Rice, Plantain, Banana, Cashew</li>
        <li>Oil Palm cultivation and processing</li>
        <li>Rice farming</li>
        <li>Development of allied industries</li>
        <li>Development of structured cottage and large-scale agro-based industries</li>
        <li>Development and processing of agricultural produce for the export markets</li>
        <li>Development of local and export oriented storage facilities and packaging plants</li>
        <li>Production and processing of a variety of agricultural products</li>
      </ul>
    </section>
  </main>

  <div class="photo-row">
    <div class="photo photo-factory" role="img" aria-label="Workers in a bright processing plant beside stainless steel tanks and pipework"></div>
    <div class="photo photo-farm" role="img" aria-label="Green crop field with tall plants under a pale sky"></div>
  </div>
</div>
</body>
</html>
```